Halberd Guard Services

Our Company is a security business which needs a cut edge design, the final product should have all relevant information and maintain a bold but modern and professional look.

Target Market(s)

A cut edge design which will attract any audience

Industry/Entity Type

Security

Contact Information for Business Card

HALBERD GUARD SERVICES

Gregor Lindqvist
Operations Manager
Phone: 0491 735 219

Email: info@halberdguard.com.au
Web: www.halberdguard.com.au

Requirements
Must have
• Must be double sided and contain all relevant information and the company logo.

```html
<!DOCTYPE html>
<html lang="en">
<head>
<meta charset="utf-8">
<title>Halberd Guard Services – Business Card</title>
<link rel="stylesheet" href="https://fonts.googleapis.com/css2?family=Arimo:wght@400;700&display=swap">
<style>
  :root {
    --page-bg: #e9eaeb;
    --card-white: #ffffff;
    --card-shade: #eef0f1;
    --slate: #46636c;
    --slate-dark: #34494f;
    --orange: #f39a1e;
    --ink: #1e1e1e;
    --ink-soft: #3a3a3a;
  }
  * { margin: 0; padding: 0; box-sizing: border-box; }
  html, body {
    width: 1200px; height: 951px; overflow: hidden;
    background: var(--page-bg);
    font-family: "Arimo", Arial, sans-serif;
  }
  .canvas { position: relative; width: 1200px; height: 951px; }

  .card {
    position: absolute;
    width: 580px; height: 330px;
    border-radius: 22px;
    background: var(--card-white);
    box-shadow: 0 10px 28px rgba(0,0,0,.18);
    overflow: hidden;
  }

  /* Front */
  .card-front {
    left: 90px; top: 90px;
    background: radial-gradient(ellipse at 55% 30%, var(--card-white) 0%, var(--card-white) 40%, var(--card-shade) 100%);
  }
  .front-brand {
    position: absolute; left: 0; right: 0; top: 84px;
    display: flex; flex-direction: column; align-items: center; gap: 20px;
  }
  .brand-mark {
    width: 62px; height: 62px; background: var(--slate);
  }
  .brand-name {
    font-weight: 700; color: var(--slate);
    font-size: 30px; letter-spacing: 1px; line-height: 1;
    white-space: nowrap;
  }
  .front-web {
    position: absolute; left: 0; right: 0; bottom: 36px;
    text-align: center;
    font-size: 19px; letter-spacing: 2px; color: var(--ink-soft);
  }

  /* Back */
  .card-back { left: 530px; top: 520px; }
  .back-brand {
    position: absolute; left: 44px; top: 30px;
    display: flex; flex-direction: column; align-items: center; gap: 10px;
  }
  .back-brand .brand-mark { width: 42px; height: 42px; }
  .back-brand .brand-name { font-size: 18px; letter-spacing: .5px; }

  .holder { position: absolute; right: 40px; top: 62px; text-align: left; }
  .holder-name { font-size: 20px; color: var(--ink); }
  .holder-role { font-size: 15px; color: var(--orange); margin-top: 2px; }

  .address {
    position: absolute; left: 44px; top: 176px;
    display: flex; gap: 8px;
    font-size: 17px; line-height: 1.25; color: var(--ink);
  }
  .contacts {
    position: absolute; left: 316px; top: 172px;
    list-style: none; font-size: 16px; line-height: 1.3; color: var(--ink);
  }
  .contacts li { display: flex; align-items: center; gap: 8px; }
  .icon { width: 14px; height: 14px; flex: none; fill: var(--orange); }
  .address .icon { margin-top: 2px; }

  .back-rule {
    position: absolute; left: 0; right: 0; bottom: 44px;
    height: 2px; background: var(--orange);
  }
  .back-band {
    position: absolute; left: 0; right: 0; bottom: 0;
    height: 40px;
    background: linear-gradient(180deg, var(--slate) 0%, var(--slate-dark) 100%);
  }
</style>
</head>
<body>
<main class="canvas">

  <section class="card card-front" aria-label="Card front">
    <div class="front-brand">
      <span class="brand-mark" aria-hidden="true"></span>
      <span class="brand-name">HALBERD GUARD SERVICES</span>
    </div>
    <p class="front-web">www.halberdguard.com.au</p>
  </section>

  <section class="card card-back" aria-label="Card back">
    <div class="back-brand">
      <span class="brand-mark" aria-hidden="true"></span>
      <span class="brand-name">HALBERD GUARD SERVICES</span>
    </div>

    <div class="holder">
      <p class="holder-name">Gregor Lindqvist</p>
      <p class="holder-role">Operations Manager</p>
    </div>

    <div class="address">
      <svg class="icon" viewBox="0 0 14 14" aria-hidden="true"><path d="M7 1 L13 6.5 H11 V13 H8.5 V9 H5.5 V13 H3 V6.5 H1 Z"/></svg>
      <p>1480 Marlow Crest Rd.<br>unit 204 - 118<br>Kelston, QLD 4105</p>
    </div>

    <ul class="contacts">
      <li><svg class="icon" viewBox="0 0 14 14" aria-hidden="true"><path d="M3 1 L5.5 1 L6.5 4.5 L5 5.6 C5.8 7.4 6.6 8.2 8.4 9 L9.5 7.5 L13 8.5 V11 C13 12.2 12 13 10.8 13 C5.5 12.6 1.4 8.5 1 3.2 C1 2 1.8 1 3 1 Z"/></svg>0491 735 219</li>
      <li><svg class="icon" viewBox="0 0 14 14" aria-hidden="true"><path d="M3 1 H11 V5 H3 Z M1 6 H13 V11 H11 V13 H3 V11 H1 Z M4 9 V12 H10 V9 Z"/></svg>0491 735 220</li>
      <li><svg class="icon" viewBox="0 0 14 14" aria-hidden="true"><path d="M1 3 H13 V11 H1 Z M1.8 3.6 L7 7.6 L12.2 3.6" stroke="#fff" stroke-width="1"/></svg>info@halberdguard.com.au</li>
      <li><svg class="icon" viewBox="0 0 14 14" aria-hidden="true"><circle cx="7" cy="7" r="6"/></svg>www.halberdguard.com.au</li>
    </ul>

    <div class="back-rule"></div>
    <div class="back-band"></div>
  </section>

</main>
</body>
</html>
```